Velvet Pressings Techno Label Business Card

I'm looking for a very clean business card for my Velvet Pressings music label. The label focusses on techno music. The card should include:

• my name : Tomas Brandt as "Founder & CEO"
• email address: tomas@velvet-pressings.example
• web: www.velvet-pressings.example
• facebook logo + /velvetpress
• twitter logo + /velvetpress
• soundcloud logo + /velvetpressings

Feel free to include your ideas! I'm looking forward to discuss about it.

Tomas

Industry/Entity Type

Business

Contact Information for Business Card

I don't like glossy cards. Prefer matt.

Requirements
Nice to have
• Maybe on one side the complete logo, other side just the icon.
Should not have
• Flashy stuff. Must be clean and business like style.

```html
<!DOCTYPE html>
<html lang="en">
<head>
<meta charset="utf-8">
<title>Velvet Pressings Business Card</title>
<link rel="stylesheet" href="https://fonts.googleapis.com/css2?family=Open+Sans:wght@600&family=Electrolize&display=swap">
<style>
  :root {
    --backdrop: #e4e4e4;
    --paper: #ffffff;
    --paper-shade: #f3f3f3;
    --panel: #4a4a4a;
    --accent: #f26a10;
    --logo-grey: #6e6e6e;
    --ink-light: #f4f4f4;
  }
  * { margin: 0; padding: 0; box-sizing: border-box; }
  html, body { width: 1200px; height: 898px; overflow: hidden; }
  body {
    background: var(--backdrop);
    position: relative;
    font-family: "Electrolize", sans-serif;
  }
  .card {
    position: absolute;
    width: 520px;
    height: 300px;
    top: 299px;
    background: linear-gradient(135deg, var(--paper) 0%, var(--paper-shade) 100%);
    box-shadow: 0 10px 28px rgba(0,0,0,0.25);
    overflow: hidden;
  }
  .card-front { left: 50px; }
  .card-back { left: 630px; }

  .brand {
    position: absolute;
    display: flex;
    align-items: center;
    gap: 12px;
  }
  .brand-dot {
    width: 34px; height: 34px;
    border-radius: 50%;
    background: var(--accent);
    flex: none;
  }
  .brand-name {
    font-family: "Open Sans", sans-serif;
    font-weight: 600;
    color: var(--logo-grey);
    letter-spacing: -0.5px;
    white-space: nowrap;
  }
  .card-front .brand { left: 50%; top: 50%; transform: translate(-50%, -50%); }
  .card-front .brand-name { font-size: 36px; }

  .edge-strip {
    position: absolute;
    left: 0; top: 0;
    width: 9px; height: 100%;
    background: var(--panel);
  }
  .edge-strip .edge-accent {
    position: absolute;
    left: 0; top: 42%;
    width: 100%; height: 26%;
    background: var(--accent);
  }
  .card-back .brand { left: 28px; top: 50%; transform: translateY(-50%); gap: 9px; }
  .card-back .brand-dot { width: 24px; height: 24px; }
  .card-back .brand-name { font-size: 25px; }

  .contact-panel {
    position: absolute;
    right: 0; top: 0;
    width: 228px; height: 100%;
    background: var(--panel);
    color: var(--ink-light);
    padding: 18px 16px 14px 10px;
    text-align: right;
    display: flex;
    flex-direction: column;
  }
  .person-name { font-size: 16px; letter-spacing: 2px; text-transform: uppercase; }
  .person-role { font-size: 10px; letter-spacing: 1.5px; text-transform: uppercase; margin-top: 2px; }
  .address { font-size: 12px; line-height: 1.5; margin-top: 20px; }
  .contact-list { list-style: none; margin-top: auto; font-size: 11px; }
  .contact-list li {
    display: flex; justify-content: flex-end; align-items: center;
    gap: 7px; line-height: 1.8;
    white-space: nowrap;
  }
  .contact-list svg { width: 11px; height: 11px; fill: var(--ink-light); flex: none; }
  .social-mark {
    width: 10px; height: 10px;
    border-radius: 2px;
    background: var(--ink-light);
    flex: none;
    margin: 0 0.5px;
  }
</style>
</head>
<body>
  <section class="card card-front" aria-label="Business card front">
    <div class="brand">
      <span class="brand-dot"></span>
      <span class="brand-name">Velvet Pressings</span>
    </div>
  </section>

  <section class="card card-back" aria-label="Business card back">
    <div class="edge-strip"><span class="edge-accent"></span></div>
    <div class="brand">
      <span class="brand-dot"></span>
      <span class="brand-name">Velvet Pressings</span>
    </div>
    <div class="contact-panel">
      <p class="person-name">Tomas Brandt</p>
      <p class="person-role">Founder &amp; CEO</p>
      <p class="address">214 KL Birch Road,<br>2nd building Lane w.</p>
      <ul class="contact-list">
        <li>012 555 0189
          <svg viewBox="0 0 24 24"><path d="M6.6 10.8a15 15 0 0 0 6.6 6.6l2.2-2.2a1 1 0 0 1 1-.25 11.4 11.4 0 0 0 3.6.57 1 1 0 0 1 1 1V20a1 1 0 0 1-1 1A17 17 0 0 1 3 4a1 1 0 0 1 1-1h3.5a1 1 0 0 1 1 1c0 1.25.2 2.45.57 3.57a1 1 0 0 1-.25 1z"/></svg>
        </li>
        <li>/velvetpress <span class="social-mark" aria-hidden="true"></span></li>
        <li>/velvetpress <span class="social-mark" aria-hidden="true"></span></li>
        <li>/velvetpressings <span class="social-mark" aria-hidden="true"></span></li>
        <li>tomas@velvet-pressings.example
          <svg viewBox="0 0 24 24"><path d="M2 5h20v14H2zm2 2v.5l8 5 8-5V7zm0 2.8V17h16V9.8l-8 5z"/></svg>
        </li>
        <li>www.velvet-pressings.example
          <svg viewBox="0 0 24 24"><path d="M12 2a10 10 0 1 0 0 20 10 10 0 0 0 0-20zm6.9 6h-2.8a15 15 0 0 0-1.3-3.6A8 8 0 0 1 18.9 8zM12 4c.9 1.2 1.6 2.5 2 4h-4c.4-1.5 1.1-2.8 2-4zM4.3 14a8 8 0 0 1 0-4h3.3a16 16 0 0 0 0 4zm.8 2h2.8c.3 1.3.8 2.5 1.3 3.6A8 8 0 0 1 5.1 16zm2.8-8H5.1a8 8 0 0 1 4.1-3.6C8.7 5.5 8.2 6.7 7.9 8zM12 20c-.9-1.2-1.6-2.5-2-4h4c-.4 1.5-1.1 2.8-2 4zm2.3-6H9.7a14 14 0 0 1 0-4h4.6a14 14 0 0 1 0 4zm.5 5.6c.5-1.1 1-2.3 1.3-3.6h2.8a8 8 0 0 1-4.1 3.6zm1.6-5.6a16 16 0 0 0 0-4h3.3a8 8 0 0 1 0 4z"/></svg>
        </li>
      </ul>
    </div>
  </section>
</body>
</html>
```